Gobal construction supply company needs new business card design

I need a business card design for my global supply company using an existing logo. i will be looking to print these on rounded corner cards with the black background version of my logo on the back. on the front white background, my logo again and my simple details.

```html
<!DOCTYPE html>
<html lang="en">
<head>
<meta charset="utf-8">
<title>Meridian Supply Works – Business Card</title>
<link rel="stylesheet" href="https://fonts.googleapis.com/css2?family=Montserrat:wght@600;700&family=Open+Sans:wght@400;600&display=swap">
<style>
  :root {
    --backdrop: #3b322d;
    --card-white: #f7f7f5;
    --card-black: #111111;
    --ink: #1c1c1c;
    --ink-soft: #3d3d3d;
    --accent-red: #e0141b;
    --rule-grey: #c9c9c9;
    --logo-white: #f2f2f2;
  }
  * { box-sizing: border-box; margin: 0; padding: 0; }
  html, body {
    width: 1200px; height: 844px; overflow: hidden;
    background: var(--backdrop);
  }
  .stage {
    position: relative; width: 1200px; height: 844px;
    display: flex; align-items: center; justify-content: center; gap: 60px;
  }
  .card {
    position: relative; width: 500px; height: 286px;
    border-radius: 6px;
    box-shadow: 0 10px 24px rgba(0,0,0,.35);
  }
  .card--front { background: var(--card-white); }
  .card--back {
    background: var(--card-black);
    display: flex; align-items: center; justify-content: center;
  }
  .brand {
    display: flex; align-items: center; gap: 10px;
    font-family: "Montserrat", sans-serif; font-weight: 700;
    text-transform: uppercase; letter-spacing: .01em;
  }
  .brand__dot {
    width: 14px; height: 14px; border-radius: 50%;
    background: var(--accent-red); flex: none;
  }
  .card--front .brand {
    position: absolute; top: 44px; right: 44px;
    font-size: 19px; color: var(--ink);
  }
  .card--back .brand { font-size: 27px; color: var(--logo-white); }
  .front__rule {
    position: absolute; left: 32px; right: 32px; top: 106px;
    height: 1px; background: var(--rule-grey);
  }
  .person {
    position: absolute; left: 32px; top: 160px;
    font-family: "Open Sans", sans-serif;
  }
  .person__name {
    font-family: "Montserrat", sans-serif; font-weight: 600;
    font-size: 17px; color: var(--accent-red); text-transform: uppercase;
    letter-spacing: .02em;
  }
  .person__title { font-size: 12.5px; color: var(--ink-soft); margin-top: 1px; }
  .contact {
    position: absolute; left: 32px; right: 32px; top: 210px;
    border-top: 1px solid var(--rule-grey); padding-top: 10px;
    font-family: "Open Sans", sans-serif; font-size: 12px; color: var(--ink-soft);
    line-height: 1.6;
  }
  .contact__row { display: flex; gap: 12px; white-space: nowrap; }
  .contact__label { color: var(--accent-red); font-weight: 600; }
  .contact__web { color: var(--accent-red); }
</style>
</head>
<body>
<main class="stage">
  <section class="card card--front" aria-label="Business card front">
    <div class="brand"><span class="brand__dot"></span><span>Meridian Supply Works</span></div>
    <div class="front__rule"></div>
    <div class="person">
      <p class="person__name">Daniel Harper</p>
      <p class="person__title">Managing Director</p>
    </div>
    <div class="contact">
      <p class="contact__row">
        <span><span class="contact__label">T:</span>(061) 555 210 480</span>
        <span><span class="contact__label">F:</span>(061) 555210481</span>
        <span><span class="contact__label">M:</span>(061) 555210482</span>
      </p>
      <p class="contact__row">
        <span><span class="contact__label">E:</span>hello@meridianworks.com</span>
        <span class="contact__web">www.meridianworks.com</span>
      </p>
    </div>
  </section>

  <section class="card card--back" aria-label="Business card back">
    <div class="brand"><span class="brand__dot"></span><span>Meridian Supply Works</span></div>
  </section>
</main>
</body>
</html>
```